Gaming packaging design for headphones

We need a striking gaming packaging.

Two versions of the logo are attached. Use the one that seems better to you for your proposal.

We like special effects on packaging, such as UV print or similar.

We don’t want packaging with openings.

Target Market(s)

Gamers

Requirements
Must have
• - Technical specifications on 6 languages, below English version:
Speaker: 50MM
Impedance: 32Ω±15%
Sensitivity: 116dB±3db
Frequency Response: 20Hz to 20KHZ
Microphone: Ф6.0*5.0MM
Cable Length: 2.0M
Plug: 3.5MM*2+USB
Size: 180*110*210mm
Weight: 356g
Backlight: RGB

- Barcode

- Certificates (CE, RoHS)

```html
<!DOCTYPE html>
<html lang="en">
<head>
<meta charset="utf-8">
<title>Nova Play – Gaming Headphones Packaging</title>
<link rel="stylesheet" href="https://fonts.googleapis.com/css2?family=Audiowide&family=Oswald:wght@300;400;500&family=Open+Sans:wght@700&display=swap">
<style>
  :root {
    --bg: #e4e4e8;
    --panel: #111213;
    --panel-edge: #1c1d1f;
    --lime: #9be21c;
    --lime-light: #c6f03a;
    --white: #f2f2f2;
    --grey-text: #c9c9c9;
    --ink: #111111;
  }
  * { box-sizing: border-box; margin: 0; padding: 0; }
  html, body { width: 1200px; height: 893px; overflow: hidden; }
  body {
    background: var(--bg);
    font-family: "Oswald", sans-serif;
    position: relative;
  }
  .dieline {
    position: absolute;
    left: 113px; top: 66px;
    display: flex;
    box-shadow: 0 10px 30px rgba(0,0,0,.25);
  }
  .face {
    position: relative;
    height: 760px;
    background: linear-gradient(135deg, var(--panel-edge), var(--panel) 60%);
    color: var(--white);
    overflow: hidden;
  }
  .face--front { width: 367px; border-right: 1px solid #2a2b2d; }
  .face--side { width: 600px; }

  .base-band {
    position: absolute; left: 0; right: 0; bottom: 0;
    height: 84px;
    background: linear-gradient(90deg, var(--lime), var(--lime-light));
    color: var(--ink);
    display: flex; align-items: center;
  }

  .brand {
    font-family: "Audiowide", sans-serif;
    color: var(--white);
    letter-spacing: 1px;
    line-height: 1;
  }
  .face--front .brand {
    position: absolute; top: 80px; width: 100%;
    text-align: center; font-size: 34px;
  }
  .front-title {
    position: absolute; top: 160px; left: 0; width: 100%;
    text-align: center;
  }
  .kicker {
    font-weight: 300; font-size: 20px; letter-spacing: 1px;
    text-transform: uppercase; color: var(--white); line-height: 1.3;
  }
  .title-main {
    font-family: "Audiowide", sans-serif;
    font-size: 50px; line-height: 1.05; color: #d8d8d8;
  }
  .title-sub {
    font-family: "Audiowide", sans-serif;
    font-size: 31px; line-height: 1.2; color: var(--lime);
  }
  .product-shot {
    position: absolute; left: 60px; top: 345px;
    width: 247px; height: 300px;
    border-radius: 40px;
    background: radial-gradient(circle at 50% 65%, #4a3a1e 0%, #2a2a2a 45%, #151515 75%);
  }
  .face--front .base-band { justify-content: center; }
  .site {
    font-family: "Open Sans", sans-serif; font-weight: 700; font-size: 17px;
  }

  .side-title { position: absolute; left: 70px; top: 30px; }
  .side-title .kicker { font-size: 22px; }
  .side-title .title-main { font-size: 58px; }
  .side-title .title-sub { font-size: 48px; }
  .badge {
    position: absolute; right: 32px; top: 82px; text-align: center;
  }
  .badge-chip {
    background: var(--lime); color: var(--ink);
    font-family: "Open Sans", sans-serif; font-weight: 700; font-size: 13px;
    padding: 5px 10px; border-radius: 4px;
  }
  .badge-size { font-size: 10px; margin-top: 4px; letter-spacing: .5px; }

  .specs {
    position: absolute; left: 62px; top: 200px;
    list-style: none;
  }
  .spec { display: flex; align-items: center; height: 56px; }
  .spec-icon {
    width: 46px; height: 46px; border-radius: 50%;
    background: radial-gradient(circle, var(--lime-light), var(--lime));
    border: 3px solid #e8ffb0;
    display: flex; align-items: center; justify-content: center;
    margin-right: 16px; flex: none;
  }
  .spec-icon svg { width: 24px; height: 24px; }
  .spec-label { font-weight: 400; font-size: 16px; color: var(--grey-text); line-height: 1.2; }
  .spec-value { font-weight: 500; font-size: 16px; line-height: 1.2; }

  .side-shot {
    position: absolute; right: 20px; top: 300px;
    width: 250px; height: 360px;
    border-radius: 120px 120px 60px 60px;
    background: radial-gradient(circle at 60% 65%, #3d4a20 0%, #262626 45%, #141414 80%);
  }
  .side-brand {
    position: absolute; left: 62px; top: 618px;
    font-size: 34px;
  }
  .face--side .base-band { padding-left: 62px; }
  .weight { font-family: "Open Sans", sans-serif; font-weight: 700; font-size: 20px; }
</style>
</head>
<body>
  <main class="dieline">
    <section class="face face--front">
      <div class="brand">NOVA PLAY</div>
      <div class="front-title">
        <p class="kicker">Over-the-ear headphones</p>
        <p class="title-main">GAMING</p>
        <p class="title-sub">HEADPHONES</p>
      </div>
      <div class="product-shot" role="img" aria-label="Photo of the gaming headset ear cup with RGB honeycomb lighting"></div>
      <div class="base-band"><span class="site">www.novaplay-gear.com</span></div>
    </section>

    <section class="face face--side">
      <div class="side-title">
        <p class="kicker">Over-the-ear headphones</p>
        <p class="title-main">GAMING</p>
        <p class="title-sub">HEADPHONES</p>
      </div>
      <div class="badge">
        <div class="badge-chip">RGB Backlight</div>
        <div class="badge-size">SIZE: 180*110*210MM</div>
      </div>

      <ul class="specs">
        <li class="spec">
          <span class="spec-icon"><svg viewBox="0 0 24 24" fill="#111"><path d="M3 9h4l5-4v14l-5-4H3z"/><path d="M15 8q3 4 0 8M18 5q5 7 0 14" stroke="#111" stroke-width="2" fill="none"/></svg></span>
          <div><p class="spec-label">Speaker:</p><p class="spec-value">50MM</p></div>
        </li>
        <li class="spec">
          <span class="spec-icon"><svg viewBox="0 0 24 24" fill="none" stroke="#111" stroke-width="2"><circle cx="12" cy="12" r="8"/><path d="M6 18L18 6"/></svg></span>
          <div><p class="spec-label">Impedance:</p><p class="spec-value">32Ω±15%</p></div>
        </li>
        <li class="spec">
          <span class="spec-icon"><svg viewBox="0 0 24 24" fill="none" stroke="#111" stroke-width="2"><circle cx="12" cy="12" r="9"/><circle cx="12" cy="12" r="4" fill="#111"/></svg></span>
          <div><p class="spec-label">Sensitivity:</p><p class="spec-value">116dB±3db</p></div>
        </li>
        <li class="spec">
          <span class="spec-icon"><svg viewBox="0 0 24 24" fill="none" stroke="#111" stroke-width="2"><path d="M2 12h5l2-6 3 12 3-9 2 3h5"/></svg></span>
          <div><p class="spec-label">Frequency Response:</p><p class="spec-value">20Hz to 20KHZ</p></div>
        </li>
        <li class="spec">
          <span class="spec-icon"><svg viewBox="0 0 24 24" fill="none" stroke="#111" stroke-width="2"><rect x="9" y="3" width="6" height="11" rx="3" fill="#111"/><path d="M6 11q0 6 6 6t6-6M12 17v4"/></svg></span>
          <div><p class="spec-label">Microphone:</p><p class="spec-value">Ф6.0*5.0MM</p></div>
        </li>
        <li class="spec">
          <span class="spec-icon"><svg viewBox="0 0 24 24" fill="none" stroke="#111" stroke-width="2"><path d="M7 3v10q0 5 5 5t5-5V11q0-3-3-3"/><path d="M12 18v3"/></svg></span>
          <div><p class="spec-label">Cable Length:</p><p class="spec-value">2.0M</p></div>
        </li>
        <li class="spec">
          <span class="spec-icon"><svg viewBox="0 0 24 24" fill="none" stroke="#111" stroke-width="2"><path d="M4 20l5-5M9 9l6 6M11 7l6 6-4 4-6-6zM14 4l-2 3M20 10l-3 2"/></svg></span>
          <div><p class="spec-label">Plug:</p><p class="spec-value">3.5MM*2+USB</p></div>
        </li>
      </ul>

      <div class="side-shot" role="img" aria-label="Photo of the black gaming headset with microphone and RGB lit ear cups"></div>
      <div class="brand side-brand">NOVA PLAY</div>
      <div class="base-band"><span class="weight">Weight: 356g</span></div>
    </section>
  </main>
</body>
</html>
```